Business card for law firm

Need business card for new law firm. Think confident, authoritative, conservative, but not stuffy or old-fashioned.

Contact Information for Business Card

Content for card - logo (uploaded), plus the following:

Paul Whitcombe (larger font)
Managing Partner (larger font, but not as large as name)
Level 9, 7 Ferris Lane
Sydney NSW 2000
Main Tel 02 9364 2710
Direct Tel 02 8472 3159
Email paul@qvlegal.com.au
www.qvlegal.com.au

Letterhead design should include logo plus:
Level 9, 7 Ferris Lane
Sydney NSW 2000
Tel 02 8472 3159
www.qvlegal.com.au

```html
<!DOCTYPE html>
<html lang="en">
<head>
<meta charset="utf-8">
<title>Quayvale Legal – Business Card</title>
<link href="https://fonts.googleapis.com/css2?family=Open+Sans:wght@400;600;700&display=swap" rel="stylesheet">
<style>
  :root {
    --stage: #1c1c1e;
    --card-black: #0b0b0c;
    --navy: #0f1f63;
    --navy-light: #1c318a;
    --ink: #111111;
    --white: #ffffff;
    --muted: #d8dcea;
  }
  * { box-sizing: border-box; margin: 0; padding: 0; }
  html, body {
    width: 1200px; height: 960px; overflow: hidden;
    background: var(--stage);
    font-family: "Open Sans", Arial, sans-serif;
  }
  .sheet {
    width: 1200px; height: 960px;
    display: flex; flex-direction: column; align-items: center; justify-content: center;
    gap: 60px;
  }
  .card {
    position: relative;
    width: 640px; height: 390px;
    overflow: hidden;
    border-radius: 4px;
    box-shadow: 0 10px 30px rgba(0,0,0,.45);
  }
  /* Back */
  .card--back {
    background: var(--card-black);
    color: var(--white);
    display: flex; flex-direction: column; align-items: center; justify-content: center;
  }
  .brand {
    display: flex; align-items: center; gap: 14px;
  }
  .brand__mark { width: 22px; height: 22px; background: var(--white); }
  .brand__name {
    font-weight: 600; font-size: 34px; letter-spacing: 2px; color: var(--white);
  }
  .card--back .web {
    margin-top: 54px; font-size: 15px; letter-spacing: 4px; color: var(--white);
  }
  /* Front */
  .card--front { background: var(--white); }
  .card__shape { position: absolute; inset: 0; width: 100%; height: 100%; }
  .card--front .brand { position: absolute; left: 48px; top: 120px; }
  .card--front .brand__mark { background: var(--navy); }
  .card--front .brand__name { color: var(--ink); font-size: 30px; }
  .contact {
    position: absolute; right: 26px; top: 38px;
    text-align: right; color: var(--white);
  }
  .contact__name { font-size: 22px; font-weight: 700; }
  .contact__role { font-size: 16px; color: var(--muted); margin-top: 2px; }
  .contact__address { margin-top: 40px; font-size: 16px; line-height: 1.3; }
  .contact__lines { margin-top: 14px; font-size: 16px; line-height: 1.45; list-style: none; }
  .contact__lines li { display: flex; align-items: center; justify-content: flex-end; gap: 8px; }
  .icon { width: 14px; height: 14px; flex: none; }
</style>
</head>
<body>
<main class="sheet">

  <section class="card card--back" aria-label="Card back">
    <div class="brand">
      <span class="brand__mark"></span>
      <span class="brand__name">Quayvale Legal</span>
    </div>
    <p class="web">www.qvlegal.com.au</p>
  </section>

  <section class="card card--front" aria-label="Card front">
    <svg class="card__shape" viewBox="0 0 640 390" preserveAspectRatio="none" aria-hidden="true">
      <path fill="var(--ink)" d="M372 0 C410 110 395 205 300 275 C245 315 190 340 150 390 L640 390 L640 0 Z"/>
      <path fill="var(--navy-light)" d="M392 0 C428 115 410 215 318 285 C262 325 215 350 182 390 L640 390 L640 0 Z"/>
      <path fill="var(--navy)" d="M400 0 C436 118 420 220 330 290 C276 330 232 355 205 390 L640 390 L640 0 Z"/>
    </svg>

    <div class="brand">
      <span class="brand__mark"></span>
      <span class="brand__name">Quayvale Legal</span>
    </div>

    <div class="contact">
      <p class="contact__name">Paul Whitcombe</p>
      <p class="contact__role">Managing Partner</p>
      <p class="contact__address">Level 9, 7 Ferris Lane<br>Sydney NSW 2000</p>
      <ul class="contact__lines">
        <li>02 9364 2710(Main)
          <svg class="icon" viewBox="0 0 14 14"><circle cx="7" cy="7" r="6.5" fill="var(--white)"/><path d="M4.5 3.5 L6 3.5 L6.5 5.5 L5.6 6.2 Q6.6 7.9 7.8 8.4 L8.5 7.5 L10.5 8 L10.5 9.5 Q6.5 10.5 4.5 3.5Z" fill="var(--navy)"/></svg>
        </li>
        <li>02 8472 3159(Direct)
          <svg class="icon" viewBox="0 0 14 14"><circle cx="7" cy="7" r="6.5" fill="var(--white)"/><path d="M4.5 3.5 L6 3.5 L6.5 5.5 L5.6 6.2 Q6.6 7.9 7.8 8.4 L8.5 7.5 L10.5 8 L10.5 9.5 Q6.5 10.5 4.5 3.5Z" fill="var(--navy)"/></svg>
        </li>
        <li>paul@qvlegal.com.au
          <svg class="icon" viewBox="0 0 14 14"><circle cx="7" cy="7" r="6.5" fill="var(--white)"/><rect x="3.5" y="4.5" width="7" height="5" fill="none" stroke="var(--navy)" stroke-width="1"/><path d="M3.5 4.5 L7 7.5 L10.5 4.5" fill="none" stroke="var(--navy)" stroke-width="1"/></svg>
        </li>
        <li>www.qvlegal.com.au
          <svg class="icon" viewBox="0 0 14 14"><circle cx="7" cy="7" r="6.5" fill="var(--white)"/><circle cx="7" cy="7" r="4" fill="none" stroke="var(--navy)" stroke-width="1"/><path d="M3 7 H11 M7 3 V11" stroke="var(--navy)" stroke-width="0.8"/></svg>
        </li>
      </ul>
    </div>
  </section>

</main>
</body>
</html>
```